"Tandem Mouthguards " Custom-made Mouthguard Business Website

We need an informational website for our mouthguard Business "Tandem Mouthguards". The logo is navy blue/lime green so want to have colour scheme that goes nicely with this - have uploaded our mouthguard flyer with some information we need to put into the website but I do have more information to put in there.

Target Market(s)

Sports clubs, sportspeople, parents and kids, schools

Industry/Entity Type

Dental, Custom-made Sports Mouthguards

Coding

Coded - Design and coding required

Number of Pages Required

5+ page

Font styles to use
Serif
Sans Serif

Colors
0054AA
0677BA
7BADD7
CADEEF
E8F1F8
0094D4
00A9DD
6FCCEA
C7EBF8
E9F6FB
00AB8E
00BBA5
67D7C9
C6EFE9
E9F9F6
59FF00
82FF00
B8FF75
E3FFCB
F4FFEA
FFF300
FFF600
FEFA6F
FFFEC7
FFFEE8
FFC000
F8CF3A
FAE287
FDF2CF
FEFAEE
F0912C
F2A743
F7CA91
FBE8D2
FDF5EE
EE7325
F08F49
F5BC92
FAE3D3
FDF4ED

Requirements
Must have
• I want drop down pages, not one scrolling page. Different pages for each heading . Content uploaded - We need a general home page with lots of pictures and info that I'll provide. A page each dedicated to 1) About Us 2) Why choose a custom mouthguard? 3) Gallery 4) Contact Us. Will need logos from "Velora"
Nice to have
• Mainly use greens and blues, but happy to pop in some yellow/oranges/red oranges if it looks good

```html
<!DOCTYPE html>
<html lang="en">
<head>
<meta charset="utf-8">
<title>Tandem Mouthguards – Custom-Made Sports Mouthguards</title>
<link href="https://fonts.googleapis.com/css2?family=Archivo+Black&family=Montserrat:wght@400;500;600;700;800&display=swap" rel="stylesheet">
<style>
:root{
  --navy:#0c1f5e;
  --green:#2cb72a;
  --green-dark:#1f9e1e;
  --mint:#e6f6e3;
  --mist:#efeff6;
  --ink:#2a2a35;
  --white:#ffffff;
  --line:#cfd3e6;
}
*{box-sizing:border-box;margin:0;padding:0}
html,body{width:1200px;height:4435px;overflow:hidden}
body{position:relative;font-family:"Montserrat",sans-serif;color:var(--ink);background:var(--white)}
.abs{position:absolute}
.display{font-family:"Archivo Black",sans-serif;letter-spacing:.5px}
.brand{display:flex;align-items:center;gap:10px;font-family:"Archivo Black",sans-serif;color:var(--navy)}
.brand-name{display:block}
.brand-dot{width:16px;height:16px;border-radius:50%;background:var(--green);flex:none}
.btn{position:absolute;display:flex;align-items:center;justify-content:center;background:var(--green);color:var(--white);font-weight:800;border-radius:30px;text-transform:uppercase;letter-spacing:.5px}
.rule{width:84px;height:2px;background:var(--green)}

/* header */
.site-header{left:0;top:0;width:1200px;height:107px;background:var(--white)}
.site-header .brand{position:absolute;left:150px;top:26px;font-size:19px;line-height:22px}
.main-nav{position:absolute;left:443px;top:42px;display:flex;gap:36px;font-size:15px;font-weight:600;color:var(--navy)}
.main-nav .active{color:var(--green);border-bottom:2px solid var(--green);padding-bottom:6px}

/* hero */
.hero{left:0;top:107px;width:1200px;height:620px;overflow:hidden}
.hero-photo{position:absolute;inset:0;background:linear-gradient(100deg,#3e5231 0%,#5d7048 35%,#8aa06a 60%,#a9b98c 80%,#6d7f57 100%)}
.hero-title{left:150px;top:78px;font-size:50px;line-height:56px;color:var(--green)}
.hero-sub{left:150px;top:198px;font-size:31px;line-height:38px;color:var(--white);font-weight:800}
.hero-tag{left:150px;top:290px;font-size:22px;line-height:33px;color:var(--white);font-weight:700}
.hero .btn{left:150px;top:393px;width:234px;height:60px;font-size:22px}
.dots{left:560px;top:553px;display:flex;gap:12px}
.dots span{width:9px;height:9px;border-radius:50%;background:var(--white)}
.dots span:first-child{background:var(--green)}

/* why choose */
.why-photo{left:152px;top:797px;width:388px;height:558px;border-radius:10px;background:linear-gradient(160deg,#f2f2f0,#e6d7b4 60%,#e8c94a)}
.why-title{left:574px;top:792px;font-size:32px;color:var(--navy)}
.why-rule{left:574px;top:846px}
.feature{position:absolute;border:1.5px solid var(--navy);border-radius:8px;background:var(--white);display:flex;flex-direction:column;align-items:center;justify-content:flex-end;text-align:center;font-size:14px;font-weight:500;line-height:19px;color:var(--navy);padding:0 26px 26px}
.feature svg{margin-bottom:20px}
.feature.wide{flex-direction:row;justify-content:center;align-items:center;text-align:left;gap:26px;padding:0}
.feature.wide svg{margin:0}

.welcome-band{left:0;top:1355px;width:1200px;height:600px;background:var(--mist)}
.gap-pill{left:238px;top:1393px;width:720px;height:57px;border-radius:30px;background:var(--mint);display:flex;align-items:center;justify-content:center;font-size:14px;color:var(--navy)}
.welcome-mark{left:150px;top:1546px;width:74px;height:74px}
.welcome-title{left:243px;top:1540px;font-size:33px;line-height:42px;color:var(--navy)}
.welcome-title span{color:var(--green)}
.welcome-copy{left:152px;top:1675px;width:380px;font-size:13px;line-height:19.5px;color:var(--ink)}
.welcome-btn{left:157px;top:1862px;width:160px;height:41px;font-size:15px}
.welcome-photo{left:555px;top:1640px;width:530px;height:275px;border-radius:40px;background:radial-gradient(ellipse at 50% 55%,#e4433c 0%,#3f7fd6 42%,rgba(239,239,246,0) 72%)}

/* process */
.process{left:0;top:2000px;width:1200px;height:655px;background-color:var(--white);background-image:linear-gradient(#eceef3 1px,transparent 1px),linear-gradient(90deg,#eceef3 1px,transparent 1px);background-size:24px 24px}
.process-title{left:0;top:2067px;width:1200px;text-align:center;font-size:32px;color:var(--navy)}
.process-rule{left:558px;top:2132px}
.step{position:absolute;top:2185px;width:213px;height:445px}
.step-photo{position:absolute;left:0;top:0;width:213px;height:240px;border-radius:8px 8px 0 0}
.step-card{position:absolute;left:8px;top:235px;width:197px;background:var(--white);border-radius:8px;box-shadow:0 4px 14px rgba(12,31,94,.12);padding:28px 20px 20px;font-size:13px;line-height:19px;color:var(--navy);font-weight:500}
.step-badge{position:absolute;left:8px;top:-12px;background:var(--green);color:var(--white);font-size:12px;font-weight:700;padding:3px 14px;border-radius:12px}
.guard-strip{left:0;top:2660px;width:1200px;height:60px;background:linear-gradient(90deg,#7fd04a,#5fb7c6,#e46fa4,#5b7fd6,#3c79d2,#444,#f2a7c4,#d9464e,#d0435a,#3f8fd1)}

/* gallery */
.gallery{left:0;top:2770px;width:1200px;height:527px;background:var(--mist)}
.gallery-title{left:0;top:2818px;width:1200px;text-align:center;font-size:32px;color:var(--navy)}
.gallery-rule{left:558px;top:2882px}
.shot{position:absolute;top:2918px;width:216px;height:247px;border-radius:2px}
.arrow{position:absolute;top:3018px;width:44px;height:44px;border:2px solid var(--navy);border-radius:50%}
.gallery-btn{left:500px;top:3208px;width:201px;height:42px;font-size:15px}

/* cta */
.cta{left:0;top:3297px;width:1200px;height:510px;overflow:hidden}
.cta-photo{position:absolute;inset:0;background:linear-gradient(100deg,#8a6a4f 0%,#a3826a 40%,#c9a78e 70%,#d8b9a0 100%)}
.cta-title{left:150px;top:75px;font-size:40px;line-height:55px;color:var(--white)}
.cta-title span{color:var(--navy)}
.cta .btn{left:150px;top:323px;width:263px;height:58px;font-size:18px}

/* footer */
.footer-brand{left:0;top:3880px;width:1200px;justify-content:center;font-size:40px;line-height:44px;gap:16px}
.footer-brand .brand-dot{width:30px;height:30px}
.footer-line{left:290px;width:620px;height:2px;background:var(--green)}
.footer-nav{left:290px;top:4048px;width:620px;display:flex;justify-content:center;gap:36px;font-size:15px;color:var(--navy)}
.footer-contact{left:290px;top:4112px;width:620px;display:flex;justify-content:center;gap:48px;font-size:15px;color:var(--navy);align-items:center}
.footer-contact span{display:flex;align-items:center;gap:8px}
.partner{top:4200px;height:48px;display:flex;align-items:center;gap:12px;font-size:28px;color:var(--navy);font-weight:700}
.partner-dot{width:26px;height:26px;border-radius:50%;background:var(--green)}
.copyright{left:0;top:4292px;width:1200px;text-align:center;font-size:14px;color:var(--navy)}
.foot-strip{left:0;top:4350px;width:1200px;height:72px;background:linear-gradient(90deg,#e2443c,#f4b23a,#3d7fd4,#9b5ad1,#35b9c2,#f2a7c4,#3f8fd1,#1e5fc2,#e89a52,#6bb5d6,#3c4fa6)}
.foot-band{left:0;top:4422px;width:1200px;height:13px;background:var(--green)}
</style>
</head>
<body>

<header class="abs site-header">
  <div class="brand"><span class="brand-dot"></span><span class="brand-name">Tandem<br>Mouthguards</span></div>
  <nav class="main-nav">
    <span class="active">About Us</span>
    <span>Why Choose a Custom Mouthguard?</span>
    <span>Gallery</span>
    <span>Contact Us</span>
  </nav>
</header>

<section class="abs hero">
  <div class="hero-photo" role="img" aria-label="Boy in football kit running on a sports field wearing a blue mouthguard"></div>
  <h1 class="abs hero-title display">TANDEM<br>MOUTHGUARDS</h1>
  <p class="abs hero-sub">Custom-Made Sports<br>Mouthguards in Perth</p>
  <p class="abs hero-tag">Protect your smile with a<br>comfortable, professional fit</p>
  <a class="btn">Book Now</a>
  <div class="abs dots"><span></span><span></span><span></span><span></span></div>
  <svg class="abs" style="left:0;top:510px" width="1200" height="110" viewBox="0 0 1200 110" aria-hidden="true">
    <path d="M0 40 Q600 150 1200 30 L1200 110 L0 110Z" fill="#fff"/>
    <path d="M0 42 Q600 150 1200 28" fill="none" stroke="#2cb72a" stroke-width="5"/>
    <path d="M0 60 Q600 170 1200 50" fill="none" stroke="#2cb72a" stroke-width="3"/>
  </svg>
</section>

<section class="why">
  <div class="abs why-photo" role="img" aria-label="Child in a yellow shirt fitting a blue mouthguard"></div>
  <h2 class="abs why-title display">WHY CHOOSE US</h2>
  <div class="abs rule why-rule"></div>

  <div class="feature" style="left:575px;top:889px;width:228px;height:174px">
    <svg width="50" height="50" viewBox="0 0 50 50" fill="none" stroke="#2cb72a" stroke-width="2.5"><path d="M10 40 L28 18 L36 26 L18 44Z"/><path d="M28 18 L34 8 L42 14 L36 26"/></svg>
    Professionally made by a qualified dental prosthetist
  </div>
  <div class="feature" style="left:820px;top:889px;width:228px;height:174px">
    <svg width="56" height="44" viewBox="0 0 56 44" fill="none" stroke="#2cb72a" stroke-width="2.5"><path d="M6 20 Q28 -4 50 20 Q28 44 6 20Z"/><path d="M14 18 V26 M22 14 V28 M30 14 V28 M38 16 V26"/></svg>
    Custom fit for comfort, protection, and durability
  </div>
  <div class="feature" style="left:575px;top:1082px;width:228px;height:152px">
    <svg width="50" height="46" viewBox="0 0 50 46" fill="none" stroke="#2cb72a" stroke-width="3"><path d="M8 44 V22 A17 17 0 0 1 42 22 V44"/><path d="M16 44 V24 A9 9 0 0 1 34 24 V44"/></svg>
    Wide range of colours and designs
  </div>
  <div class="feature" style="left:820px;top:1082px;width:228px;height:152px">
    <svg width="40" height="50" viewBox="0 0 40 50" fill="none" stroke="#2cb72a" stroke-width="2.5"><circle cx="20" cy="14" r="9"/><path d="M6 48 V36 A14 10 0 0 1 34 36 V48"/></svg>
    Available for kids, teens, and adults
  </div>
  <div class="feature wide" style="left:575px;top:1250px;width:473px;height:102px">
    <svg width="60" height="50" viewBox="0 0 60 50" fill="none" stroke="#2cb72a" stroke-width="2.5"><circle cx="12" cy="10" r="5"/><path d="M6 40 V22 H18 V40"/><rect x="30" y="22" width="24" height="24"/><path d="M42 28 V40 M36 34 H48"/><circle cx="42" cy="10" r="5"/></svg>
    <span>Clinic and mobile school/club<br>visits available</span>
  </div>
</section>

<section class="welcome">
  <div class="abs welcome-band"></div>
  <svg class="abs" style="left:0;top:1355px" width="1200" height="140" viewBox="0 0 1200 140" aria-hidden="true">
    <path d="M60 0 Q90 0 100 40 Q130 140 240 140 L960 140 Q1070 140 1100 40 Q1110 0 1140 0Z" fill="#fff"/>
  </svg>
  <div class="abs gap-pill">Talk to us about our “gap free” mouthguards for eligible private health insurance members.</div>
  <svg class="abs welcome-mark" viewBox="0 0 74 74" aria-hidden="true"><circle cx="37" cy="37" r="34" fill="#2cb72a"/></svg>
  <h2 class="abs welcome-title display">WELCOME TO<br><span>TANDEM MOUTHGUARDS</span></h2>
  <p class="abs welcome-copy">Lorem ipsum dolor sit amet, consectetur adipiscing elit, sed do eiusmod tempor incididunt ut labore et dolore magna aliqua. Ut enim ad minim veniam, quis nostrud exercitation ullamco laboris nisi ut aliquip ex ea commodo consequat. Duis aute irure dolor in repre henderit in voluptate velit esse cillum dolore eu fugiat nulla pariatur. Excepteur sint occaecat cupidatat non proident, sunt in culpa qui officia deserunt mollit anim id est laborum</p>
  <a class="btn welcome-btn">Read More</a>
  <div class="abs welcome-photo" role="img" aria-label="Assortment of colourful custom mouthguards and cases"></div>
</section>

<svg class="abs" style="left:0;top:1930px" width="1200" height="90" viewBox="0 0 1200 90" aria-hidden="true">
  <path d="M0 0 Q600 120 1200 0 L1200 0 L0 0Z" fill="#efeff6"/>
  <path d="M0 8 Q600 120 1200 2" fill="none" stroke="#2cb72a" stroke-width="5"/>
  <path d="M0 24 Q600 140 1200 18" fill="none" stroke="#2cb72a" stroke-width="3"/>
</svg>

<section class="abs process"></section>
<h2 class="abs process-title display">THE PROCESS</h2>
<div class="abs rule process-rule"></div>

<div class="step" style="left:152px">
  <div class="step-photo" role="img" aria-label="Hands holding a phone to book an appointment" style="background:linear-gradient(150deg,#3a3a3f,#8b8b90 55%,#d9d9dc)"></div>
  <div class="step-card"><span class="step-badge">Step 1</span>Book an appointment or mobile visit with our dental prosthetist</div>
</div>
<div class="step" style="left:380px">
  <div class="step-photo" role="img" aria-label="Hand holding a clear dental impression" style="background:linear-gradient(150deg,#f1f1ef,#d9d7d2 60%,#e8c9b6)"></div>
  <div class="step-card"><span class="step-badge">Step 2</span>Impressions are taken of the mouth – this appointment will generally take around 15 minutes. You then get to choose your design (if you haven’t already!)</div>
</div>
<div class="step" style="left:608px">
  <div class="step-photo" role="img" aria-label="Gloved hands shaping a mouthguard on a dental model" style="background:linear-gradient(150deg,#8e9aa3,#3f5f86 55%,#c8a79a)"></div>
  <div class="step-card"><span class="step-badge">Step 3</span>Mouthguard is made in-house in our laboratory by our prosthetist and technicians.</div>
</div>
<div class="step" style="left:836px">
  <div class="step-photo" role="img" aria-label="Athlete wearing a fitted mouthguard" style="background:linear-gradient(170deg,#7fb0e0,#c9a088 60%,#eef0f3)"></div>
  <div class="step-card"><span class="step-badge">Step 4</span>Fit and collection – you may either pick up from our clinic - or for sporting clubs or schools, we can have them packed and delivered to you.</div>
</div>

<div class="abs guard-strip" role="img" aria-label="Row of colourful patterned mouthguards" style="border-radius:30px"></div>

<section class="abs gallery"></section>
<h2 class="abs gallery-title display">GALLERY</h2>
<div class="abs rule gallery-rule"></div>
<div class="arrow" style="left:76px"><svg width="40" height="40" viewBox="0 0 40 40" aria-hidden="true"><path d="M23 13 L16 20 L23 27" fill="none" stroke="#0c1f5e" stroke-width="2.5"/></svg></div>
<div class="shot" style="left:152px;background:linear-gradient(150deg,#6b5a2e,#5a2f6e 55%,#c9b98a)" role="img" aria-label="Purple glitter mouthguard in a gold case"></div>
<div class="shot" style="left:380px;background:linear-gradient(150deg,#e7e5e2,#8a2233 55%,#f3f2f0)" role="img" aria-label="Maroon school mouthguard in a white case"></div>
<div class="shot" style="left:607px;background:linear-gradient(150deg,#5a3fa2,#3bb4c0 55%,#7a5bbd)" role="img" aria-label="Teal and purple mouthguard in a purple case"></div>
<div class="shot" style="left:834px;background:linear-gradient(150deg,#4a2e8a,#d7d7e2 55%,#6a4ba6)" role="img" aria-label="Patterned mouthguard in a purple case"></div>
<div class="arrow" style="left:1078px"><svg width="40" height="40" viewBox="0 0 40 40" aria-hidden="true"><path d="M17 13 L24 20 L17 27" fill="none" stroke="#0c1f5e" stroke-width="2.5"/></svg></div>
<a class="btn gallery-btn">View All Images</a>

<section class="abs cta">
  <div class="cta-photo" role="img" aria-label="Child fitting a blue mouthguard"></div>
  <h2 class="abs cta-title display">PLEASE CONTACT US<br>TO MAKE A BOOKING<br>FOR YOUR <span>NEW CUSTOM<br>MOUTHGUARD.</span></h2>
  <a class="btn">Book Online Now</a>
  <svg class="abs" style="left:0;top:420px" width="1200" height="90" viewBox="0 0 1200 90" aria-hidden="true">
    <path d="M0 20 Q600 110 1200 0 L1200 90 L0 90Z" fill="#fff"/>
    <path d="M0 18 Q600 110 1200 0" fill="none" stroke="#2cb72a" stroke-width="5"/>
    <path d="M0 36 Q600 128 1200 18" fill="none" stroke="#2cb72a" stroke-width="3"/>
  </svg>
</section>

<footer>
  <div class="abs brand footer-brand"><span class="brand-dot"></span><span class="brand-name">Tandem<br>Mouthguards</span></div>
  <div class="abs footer-line" style="top:4032px"></div>
  <nav class="abs footer-nav"><span>About Us</span><span>Why Choose a Custom Mouthguard?</span><span>Gallery</span><span>Contact Us</span></nav>
  <div class="abs footer-line" style="top:4090px"></div>
  <div class="abs footer-contact">
    <span><svg width="16" height="16" viewBox="0 0 16 16" aria-hidden="true"><path d="M3 1 L6 1 L7 5 L5 6 Q6 9 10 11 L11 9 L15 10 L15 13 Q14 15 12 15 Q2 13 1 3 Q1 1 3 1Z" fill="#2cb72a"/></svg>+1 555 014 2270</span>
    <span><svg width="18" height="14" viewBox="0 0 18 14" aria-hidden="true"><rect x="1" y="1" width="16" height="12" fill="#2cb72a"/><path d="M1 1 L9 8 L17 1" fill="none" stroke="#fff" stroke-width="1.5"/></svg>info@tandemmouthguards.com</span>
  </div>
  <div class="abs footer-line" style="top:4150px"></div>
  <div class="abs partner" style="left:290px"><span class="partner-dot"></span>Velora</div>
  <div class="abs partner" style="left:718px;font-size:20px"><span class="partner-dot"></span>Harbour Denture Care</div>
  <p class="abs copyright">Copyright © 2025 All Rights Reserved</p>
  <div class="abs foot-strip" role="img" aria-label="Row of colourful patterned mouthguards"></div>
  <div class="abs foot-band"></div>
</footer>

</body>
</html>
```